Cruise Booking Website

Cruise search and booking website

This project is a redesign of a cruise booking website we did a few years ago.

The current website is located here: http://voyage.pylonworks.example/en/

It's not fully functional but gives you ad idea how miserable the old design was.

All the information about cruises, cruise lines, destinations, ports and shore excursions will be similar to http://www.sailquest.example/
Actual search pages (form, results, single result, sailing and cabin selection, ship info, booking) will have EXACTLY the same info as sailquest.example

We like the style of http://harborfleetdesk.example, it's quite modern, good spacing, not overloaded with information. So you can use it as an example of what we like, not what we want as a final result for us. Please, don't copy it. The result should not be possible to resemble the harborfleetdesk.example, because our site has to be unique. This is important!
If you submit a design that clearly reminds another cruise site it will be rejected!

Also the mockup provided is just to give you the basic structure and show what information has to be present on the page. It doesn't mean the layout has to be the same as a mockup. The layout is up to the designer.

I've updated the mockup to be more generic so it doesn't confuse you:
https://files.boxvault.example/s/k7m2qp9wz4hx/Home%20page.png

When you're adding social sharing icons like plazanet/chirpline you have to use chinese ones instead:
https://files.boxvault.example/s/t3nr8vx5lc2e/chinese-social-icons.png
Originals: http://minilk.example/qR7t

We'll start with home page first and after it's approved inner pages can be designed.

I know the cost of the project doesn't look high, but the task is straight forward and doesn't require to be very original, it's better to follow existing design and layout patterns that proved to work well.
That's why I encourage you to choose a template to build the design on top of one of https://themeparlor.example/ themes if it will save the design work, will be easier and faster for you. So it will be more like a customization than a new design from scratch.

Mockups, site map and logo files:
- https://files.boxvault.example/sh/h48dm2rs73fkpw/QvnbW2Xz8e

Website tree:
- https://sheets.papernest.example/document/d/7xPqR2mLw9sTk4VbN8cHj3YzA6eUf5GdKo1iMnBv/edit?usp=sharing
Updates

So far a lot of designs are just copying http://www.harborfleetdesk.example/ - we don't like it!

We like the style of harborfleetdesk.example, it's quite modern, good spacing, not overloaded with information. So you can use it as an example of what we like, not what we want as a final result for us. Please, don't copy it. The result should not be possible to resemble the harborfleetdesk.example, because our site has to be unique. This is important!

Target Market(s)

Chinese travellers

Industry/Entity Type

Build

Requirements
Must have
• * White, blue and red
* Large spacing, not too much information cramped into a small space like sailquest.example or the current website
* More "hidden" info in popups, tabs and so on, so not to many things are visible at the same time
* Compatible with kestrel scaffold styling (for easier coding):
- http://kestrelkit.codeshelf.example/scaffold/index.html
- http://skinmarket.example/
* Feel free to propose to build the design on top of one of https://themeparlor.example/ themes if it will save the design work, will be easier and faster for you

```html
<!DOCTYPE html>
<html lang="en">
<head>
<meta charset="utf-8">
<title>Seabound — Cruise Booking</title>
<link href="https://fonts.googleapis.com/css2?family=Open+Sans:wght@300;400;600;700;800&display=swap" rel="stylesheet">
<style>
:root{
  --blue-deep:#1d67ad;
  --blue-sky:#4aa9e8;
  --blue-foot:#4faeea;
  --sea:#2e6a8a;
  --sea-dark:#1f4f6b;
  --teal:#2fc4cf;
  --teal-light:#6ad7e8;
  --red:#e0483c;
  --red-dark:#c8392e;
  --grey-nav:#e6e6e6;
  --grey-card:#ececec;
  --grey-strip:#f3f3f3;
  --text:#333;
  --muted:#888;
  --white:#fff;
}
*{box-sizing:border-box;margin:0;padding:0}
html,body{width:798px;height:1200px;overflow:hidden}
body{font-family:'Open Sans',Arial,sans-serif;color:var(--text);background:var(--white);position:relative;font-size:9px}
.abs{position:absolute}

/* header */
.site-header{position:absolute;left:0;top:0;width:798px;height:89px;background:var(--sea-dark)}
.brand{position:absolute;left:31px;top:14px;display:flex;align-items:center;gap:8px}
.brand-mark{width:30px;height:30px;border-radius:50%;background:var(--white)}
.brand-name{font-size:26px;font-weight:800;color:var(--white);letter-spacing:-.5px}
.search-box{position:absolute;left:504px;top:14px;width:115px;height:15px;border-radius:8px;background:var(--white)}
.search-label{position:absolute;left:625px;top:13px;color:var(--white);font-size:12px}
.adv-search{position:absolute;left:503px;top:34px;color:#cfe3ee;font-size:9px;text-decoration:underline}
.top-links{position:absolute;left:688px;top:6px;width:80px}
.top-links a{display:block;color:var(--white);font-size:10px;text-decoration:none;border-bottom:1px solid #8fb3c6;padding:1px 0 2px;margin-bottom:2px}
.top-links a:last-child{border:0}

.main-nav{position:absolute;left:29px;top:59px;width:739px;height:29px;background:var(--grey-nav);display:flex;align-items:center;padding-left:27px;gap:0}
.main-nav a{font-size:10px;color:#222;text-decoration:none;margin-right:19px;white-space:nowrap}
.main-nav a::after{content:"";display:inline-block;width:4px;height:4px;border-right:1.3px solid var(--red);border-bottom:1.3px solid var(--red);transform:rotate(45deg);margin-left:4px;position:relative;top:-2px}

/* hero */
.hero{position:absolute;left:0;top:89px;width:798px;height:254px;background:linear-gradient(160deg,#3b7ea0 0%,#2a6585 45%,#1f5372 100%)}
.hero-photo{position:absolute;inset:0;background:linear-gradient(180deg,rgba(255,255,255,.08),rgba(0,0,0,.15))}
.hero-arrow{position:absolute;top:84px;width:25px;height:55px;background:rgba(20,50,70,.55);display:flex;align-items:center;justify-content:center}
.prize{position:absolute;left:89px;top:55px;width:139px;height:138px;border:2px solid var(--teal);background:rgba(20,70,90,.55);text-align:center;color:var(--white)}
.prize .hurry{font-size:19px;font-weight:700;color:var(--teal-light);margin-top:10px;line-height:1}
.prize .win{font-size:13px;font-weight:700;line-height:1.1}
.prize .win span{font-weight:300;color:var(--teal-light)}
.prize .amount{font-size:30px;font-weight:300;color:var(--teal);line-height:1.15}
.prize .cruise{font-size:26px;font-weight:800;line-height:1}
.prize .for{font-size:11px;color:var(--teal-light);font-weight:300;margin-top:3px}
.dest-tile{position:absolute;width:69px;height:69px;background:rgba(220,235,240,.85);padding:4px}
.dest-tile .inner{width:100%;height:100%;background:#1d6d7c;border:1px solid var(--teal-light);text-align:center;color:var(--teal-light);font-size:8px;padding-top:3px;line-height:1.05}
.dest-tile .art{width:30px;height:26px;margin:5px auto 0;background:linear-gradient(#e8f4f6,#a7d6de);border-radius:3px}
.hero-title{position:absolute;left:448px;top:47px;color:var(--teal-light);font-size:21px;font-weight:300;line-height:1.1;letter-spacing:.5px}
.find-more{position:absolute;left:468px;top:128px;width:126px;height:32px;background:linear-gradient(90deg,#c9f0f2,#52c9d6);color:#123;font-weight:800;font-size:16px;padding:6px 0 0 14px;letter-spacing:.5px}
.find-more::after{content:"›";color:var(--white);margin-left:4px}
.best-badge{position:absolute;left:424px;top:101px;width:64px;height:64px;border-radius:50%;background:var(--white);border:3px solid var(--red)}
.best-badge span{position:absolute;left:6px;top:20px;color:var(--red);font-weight:700;font-size:11px;transform:rotate(-45deg);line-height:1}

/* hotline strip */
.strip{position:absolute;left:0;top:343px;width:798px;height:88px;background:var(--grey-strip)}
.hotline{position:absolute;left:29px;top:351px;width:171px;height:37px;border:1px solid var(--blue-deep);background:var(--white);display:flex;align-items:center;padding-left:10px;gap:6px;font-size:10px}
.hotline b{font-weight:400;font-size:14px;color:#1b3d57}
.account-link{position:absolute;top:364px;font-size:10px;display:flex;align-items:center;gap:3px;color:#222}

/* feature cards */
.feature{position:absolute;top:403px;width:171px;height:140px;background:var(--grey-card)}
.feature .photo{height:93px}
.feature h3{font-size:11px;font-weight:400;margin:11px 0 0 9px}
.read-more{display:inline-flex;align-items:center;background:var(--white);margin:3px 0 0 9px;font-size:8px;color:var(--red);font-weight:600;padding-right:6px}
.read-more i{width:11px;height:11px;background:var(--red);color:var(--white);font-style:normal;font-size:10px;line-height:11px;text-align:center;margin-right:8px}

.finder{position:absolute;left:599px;top:403px;width:170px;height:139px;background:var(--white);border:1px solid #ddd}
.finder h4{background:var(--red);color:var(--white);text-align:center;font-size:11px;font-weight:600;letter-spacing:1px;height:20px;line-height:20px}
.sel{position:absolute;height:13px;border:1px solid #aaa;font-size:8px;padding-left:3px;line-height:11px;background:var(--white)}
.sel::after{content:"⬍";position:absolute;right:2px;top:0;font-size:8px;border-left:1px solid #aaa;padding-left:2px}
.finder .age{position:absolute;font-size:7px;color:#444}
.search-btn{position:absolute;left:21px;top:125px;width:130px;height:13px;background:var(--blue-deep);color:var(--white);font-size:9px;font-weight:700;text-align:center;letter-spacing:1px;line-height:13px}

/* info blocks */
.info-icon{position:absolute;top:572px;width:76px;height:76px;border:1px solid var(--red);border-radius:50%;display:flex;align-items:center;justify-content:center;color:var(--red)}
.info{position:absolute;top:660px;width:200px}
.info h3{font-size:13px;font-weight:400;color:#222}
.info p{font-size:9px;color:var(--muted);line-height:1.3;margin-top:2px}
.info p a{color:var(--red);text-decoration:none}
.divider{position:absolute;left:29px;top:755px;width:739px;height:1px;background:var(--red)}
.section-title{position:absolute;left:29px;top:757px;font-size:23px;font-weight:300;color:#444}

/* deals */
.deal{position:absolute;top:792px;width:182px;height:188px;background:var(--grey-card)}
.deal .panel{position:absolute;left:3px;right:3px;top:18px;bottom:8px;background:var(--white)}
.deal.dark .panel{background:var(--grey-card)}
.deal .head{height:35px;background:var(--blue-sky);color:var(--white);font-size:16px;font-weight:300;text-align:center;line-height:35px}
.deal.dark .head{height:47px;background:var(--blue-deep);line-height:47px}
.deal .body{padding:8px 12px 0;text-align:center;font-size:8.6px;color:#555;line-height:1.35}
.deal .body a{color:var(--red);text-decoration:none}
.plan-btn{display:inline-block;background:var(--red);color:var(--white);font-size:7.5px;font-weight:700;letter-spacing:.5px;padding:3px 11px;margin-top:9px}
.mini-deal{display:flex;gap:10px;text-align:left;margin-bottom:5px;font-size:7.8px;line-height:1.3;color:#333}
.mini-deal .thumb{width:40px;height:38px;flex:none;background:linear-gradient(#7ab6d8,#d9c7a6)}

/* partners */
.partners{position:absolute;left:0;top:1008px;width:798px;height:54px;background:var(--red)}
.partners h2{position:absolute;left:34px;top:11px;color:var(--white);font-size:21px;font-weight:300}
.partner-badge{position:absolute;top:17px;height:20px;background:rgba(255,255,255,.85);border-radius:3px}
.p-arrow{position:absolute;top:14px;color:var(--white);font-size:18px}

/* footer */
.site-footer{position:absolute;left:0;top:1062px;width:798px;height:138px;background:var(--blue-foot)}
.foot-col{position:absolute;top:22px;list-style:none}
.foot-col li{font-size:8px;color:#102a3d;height:14px}
.foot-col li::before{content:"";display:inline-block;width:3px;height:3px;background:var(--white);margin-right:7px;vertical-align:middle}
.social{position:absolute;width:19px;height:19px;border-radius:4px;background:var(--white)}
.foot-line{position:absolute;left:29px;top:100px;width:739px;height:1px;background:#2f6e96}
.copy{position:absolute;left:0;width:798px;text-align:center;font-size:8px;color:#102a3d}
</style>
</head>
<body>

<header class="site-header">
  <div class="brand"><span class="brand-mark"></span><span class="brand-name">Seabound</span></div>
  <div class="search-box"></div>
  <span class="search-label">Search</span>
  <span class="adv-search">Advance Search</span>
  <nav class="top-links"><a href="#">BOOKING</a><a href="#">ONLINE BOOKING</a><a href="#">MEMBERS CENTRE</a></nav>
  <nav class="main-nav">
    <a href="#">DESTINATIONS</a><a href="#">CRUISE LINES</a><a href="#">SHORE ACTIVITIES</a><a href="#">PROMOTIONS</a><a href="#">CRUISE NEWS</a><a href="#">BLOG</a><a href="#">FAQ(Q&amp;A)</a><a href="#">CONTACT US</a>
  </nav>
</header>

<section class="hero">
  <div class="hero-photo" role="img" aria-label="Cruise ship deck looking out over the blue sea"></div>
  <div class="hero-arrow" style="left:29px"><svg width="10" height="16"><path d="M8 2 2 8l6 6" stroke="#fff" stroke-width="2" fill="none"/></svg></div>
  <div class="hero-arrow" style="left:745px"><svg width="10" height="16"><path d="M2 2l6 6-6 6" stroke="#fff" stroke-width="2" fill="none"/></svg></div>
  <div class="prize">
    <div class="hurry">HURRY</div>
    <div class="win"><span>TO</span> WIN A</div>
    <div class="amount">$6000</div>
    <div class="cruise">CRUISE</div>
    <div class="for">VACATION FOR 2</div>
  </div>
  <div class="dest-tile" style="left:247px;top:48px"><div class="inner">MEXICO<div class="art" role="img" aria-label="Sombrero icon"></div></div></div>
  <div class="dest-tile" style="left:327px;top:48px"><div class="inner">JAPAN<div class="art" role="img" aria-label="Pagoda icon"></div></div></div>
  <div class="dest-tile" style="left:247px;top:130px"><div class="inner">WESTERN<br>CARIBBEAN<div class="art" role="img" aria-label="Palm tree icon" style="margin-top:2px"></div></div></div>
  <div class="dest-tile" style="left:327px;top:130px"><div class="inner">EUROPE<div class="art" role="img" aria-label="Tower icon"></div></div></div>
  <div class="hero-title">CRAZY CRUISE VACATIONS<br>&amp; GRAB MUCH MORE</div>
  <div class="find-more" style="padding-left:18px">FIND MORE</div>
  <div class="best-badge"><span>BEST<br>OFFERS</span></div>
</section>

<div class="strip"></div>
<div class="hotline">
  <svg width="14" height="22" viewBox="0 0 14 22"><path d="M3 1h3l1 5-2 2c1 3 2 5 4 7l2-1 3 3-2 3C6 20 1 12 2 3z" fill="#e0483c"/></svg>
  Hotline: <b>4008 512 930</b>
</div>
<div class="account-link" style="left:603px"><svg width="16" height="16" viewBox="0 0 16 16"><rect x="1" y="3" width="11" height="11" fill="none" stroke="#e0483c" stroke-width="1.5"/><path d="M6 10l8-8" stroke="#e0483c" stroke-width="2"/></svg>REGISTER</div>
<div class="account-link" style="left:692px"><svg width="16" height="16" viewBox="0 0 16 16"><rect x="4" y="1" width="10" height="13" fill="none" stroke="#e0483c" stroke-width="1.5"/><path d="M1 8h8M6 5l3 3-3 3" stroke="#e0483c" stroke-width="1.5" fill="none"/></svg>MY ACCOUNT</div>

<article class="feature" style="left:29px"><div class="photo" role="img" aria-label="Cruise ship sailing at sea" style="background:linear-gradient(#6fb6e4,#2a7bbd)"></div><h3>Cruise lines</h3><a class="read-more"><i>+</i>Read More</a></article>
<article class="feature" style="left:219px"><div class="photo" role="img" aria-label="Rocky coastline with turquoise water" style="background:linear-gradient(#9fc8e8,#3d8db0 55%,#a89a80)"></div><h3>Shore Activites</h3><a class="read-more"><i>+</i>Read More</a></article>
<article class="feature" style="left:409px"><div class="photo" role="img" aria-label="Grand theatre interior on board a ship" style="background:linear-gradient(#c99a55,#7a3f22)"></div><h3>Cruise news</h3><a class="read-more"><i>+</i>Read More</a></article>

<aside class="finder">
  <h4>FIND YOUR CRUISE</h4>
  <div class="sel" style="left:21px;top:30px;width:130px">Popular Destinations</div>
  <div class="sel" style="left:21px;top:53px;width:62px">Any Length</div>
  <div class="sel" style="left:89px;top:53px;width:62px">Any Month</div>
  <div class="sel" style="left:21px;top:76px;width:130px">Any Cruise Lines</div>
  <span class="age" style="left:21px;top:95px">AGE 25+</span>
  <span class="age" style="left:89px;top:95px">AGE 0-24</span>
  <div class="sel" style="left:21px;top:105px;width:62px">2</div>
  <div class="sel" style="left:89px;top:105px;width:62px">0</div>
  <div class="search-btn">SEARCH CRUISE</div>
</aside>

<div class="info-icon" style="left:108px"><span style="font-weight:800;font-size:16px">BLOG</span></div>
<div class="info-icon" style="left:361px"><span style="font-weight:800;font-size:42px;line-height:1">?</span></div>
<div class="info-icon" style="left:614px"><svg width="44" height="30" viewBox="0 0 44 30"><path d="M3 8c6-6 14-6 18 0l14 8c6 2 7 8 4 10H5C1 22 1 13 3 8z" fill="#e0483c"/><path d="M12 8l3 6M17 8l3 6" stroke="#fff" stroke-width="1.5"/></svg></div>

<div class="info" style="left:41px"><h3>Blog</h3><p>Lorem Ipsum is simply dummy text of the print-ing and typesetting industry. Lorem Ipsum has been the industry's standard dummy text ever since the 1500s, <a href="#">Learn More &gt;</a></p></div>
<div class="info" style="left:294px"><h3>FAQ(Q&amp;A)</h3><p>Lorem Ipsum is simply dummy text of the print-ing and typesetting industry. Lorem Ipsum has been the industry's standard dummy text ever since the 1500s, <a href="#">Learn More &gt;</a></p></div>
<div class="info" style="left:546px;top:660px"><h3>Ports</h3><p style="margin-top:0">Lorem Ipsum is simply dummy text of the print-ing and typesetting industry. Lorem Ipsum has been the industry's standard dummy text ever since the 1500s, <a href="#">Learn More &gt;</a></p></div>

<div class="divider"></div>
<h2 class="section-title">Our Deals</h2>

<div class="deal" style="left:29px"><div class="panel"><div class="head">Packages</div><div class="body">
  <svg width="22" height="22" viewBox="0 0 22 22"><rect x="3" y="8" width="16" height="12" fill="none" stroke="#e0483c" stroke-width="1.5"/><rect x="1" y="5" width="20" height="4" fill="none" stroke="#e0483c" stroke-width="1.5"/><path d="M11 5v15M11 5C8 0 4 2 7 5M11 5c3-5 7-3 4 0" stroke="#e0483c" stroke-width="1.5" fill="none"/></svg><br>
  seabound.example offers the best cruise deals and discounts on all cruise lines and cruise vacation packages world-wide. <a href="#">Learn More &gt;</a><br><span class="plan-btn">CHOOSE PLAN</span></div></div></div>

<div class="deal dark" style="left:214px"><div class="panel"><div class="head">Recommended</div><div class="body" style="padding-top:8px">
  <svg width="24" height="26" viewBox="0 0 24 26"><path d="M3 12h5v12H3zM8 13l5-11c3 0 3 3 2 7h6c2 0 2 3 1 4 1 1 1 3-1 4 1 1 0 3-2 3 0 2-1 3-3 3H8z" fill="none" stroke="#e0483c" stroke-width="1.4"/></svg><br>
  Let us put your mind at ease by answering questions about tickets, tipping, documentation, dress codes and more. <a href="#">Learn More &gt;</a><br><span class="plan-btn">CHOOSE PLAN</span></div></div></div>

<div class="deal dark" style="left:398px"><div class="panel"><div class="head">Last Minute Deals</div><div class="body" style="padding-top:8px">
  <svg width="22" height="26" viewBox="0 0 22 26"><circle cx="11" cy="15" r="9" fill="none" stroke="#e0483c" stroke-width="1.5"/><path d="M11 15V9M9 2h4M11 2v4" stroke="#e0483c" stroke-width="1.5"/></svg><br>
  Last minute cruises offer a great opportunity to get exceptional cruise deals, discounts, upgrades and other valuable offers on <a href="#">Learn More &gt;</a><br><span class="plan-btn">CHOOSE PLAN</span></div></div></div>

<div class="deal" style="left:584px"><div class="panel"><div class="head">Star Line Cruise Deals</div><div class="body" style="padding-top:6px">
  <div class="mini-deal"><div class="thumb" role="img" aria-label="Couple relaxing on a ship deck"></div><div>4-Day Sales Event Featuring Exclusive Savings plus 3rd/4th Guest FREE</div></div>
  <div class="mini-deal"><div class="thumb" role="img" aria-label="Couple dining by the sea"></div><div>FREE complimentary specialty dinner for 2 plus $50 onboard credit</div></div>
  <span class="plan-btn" style="margin-top:0">CHOOSE PLAN</span></div></div></div>

<section class="partners">
  <h2>Our Partners</h2>
  <span class="p-arrow" style="left:263px">‹</span>
  <div class="partner-badge" style="left:286px;width:70px"></div>
  <div class="partner-badge" style="left:383px;width:50px"></div>
  <div class="partner-badge" style="left:461px;width:84px"></div>
  <div class="partner-badge" style="left:574px;width:80px"></div>
  <div class="partner-badge" style="left:684px;width:62px"></div>
  <span class="p-arrow" style="left:762px">›</span>
</section>

<footer class="site-footer">
  <ul class="foot-col" style="left:98px"><li>Visa</li><li>About us</li><li>Contact us</li><li>Payment info</li></ul>
  <ul class="foot-col" style="left:259px"><li>Terms of privacy</li><li>Terms of service</li><li>Terms of insurance</li><li>Cooperation network</li></ul>
  <ul class="foot-col" style="left:445px"><li>Registration agreement</li><li>Cruise promotion policy</li><li>Booking process explanation</li><li>Bonus points collection policy</li></ul>
  <span class="social" style="left:643px;top:25px"></span>
  <span class="social" style="left:680px;top:25px"></span>
  <span class="social" style="left:643px;top:49px"></span>
  <span class="social" style="left:680px;top:49px"></span>
  <span class="social" style="left:643px;top:73px"></span>
  <span class="social" style="left:680px;top:73px"></span>
  <div class="foot-line"></div>
  <p class="copy" style="top:108px">Copyright © 2011 Seabound Voyages All rights reserved</p>
  <p class="copy" style="top:122px">Licence No. 10000000</p>
</footer>

</body>
</html>
```